New Business Card for Software Company

We are looking at rebranding a 10 year old company that specializes in PDF and DWF solutions for Architects and Engineers. We will attach the new company logo that we are going with so you can work with that and complimentary colors.
The sample information we would like on the business card is:
Gerald Pinfold
Vice President
4738 W. Harrowgate Lane. STE 305
PMB#417
Mesa, AZ 85374
866-392-5074 US Toll Free
123-456-3190 Cell
gpinfold@plavorix.com
The old tag line that we had on the business cars was.
Dependable Drawing File Tools for Architects and Engineers in Every Market.
If you have an idea for a better tag line we are open to that also.
Updates
We would like to thank all of the Designers for their wonderful work. We apologize that we will not have the time to provide feedback to everyone. There is just so many innovative and professional designs that you have all created making our decision even harder.
Target Market(s)
Architects and Engineers
Industry/Entity Type
Business
Look and feel

```html
<!DOCTYPE html>
<html lang="en">
<head>
<meta charset="utf-8">
<title>Plavorix Business Card</title>
<link rel="stylesheet" href="https://fonts.googleapis.com/css2?family=Arimo:wght@400;700&family=Open+Sans:wght@400&display=swap">
<style>
  :root {
    --stage: #e9e9ee;
    --paper: #ffffff;
    --red: #c4272f;
    --red-deep: #b81f2c;
    --orange: #f7941e;
    --orange-mid: #e8552a;
    --glow: #f58a2a;
    --ink: #333333;
    --logo-grey: #5a5a5a;
    --white: #ffffff;
  }
  * { box-sizing: border-box; margin: 0; padding: 0; }
  html, body { width: 1200px; height: 987px; overflow: hidden; }
  body {
    background: var(--stage);
    font-family: "Arimo", Arial, sans-serif;
    position: relative;
  }
  .card {
    position: absolute;
    left: 230px;
    width: 740px;
    height: 423px;
    border-radius: 28px;
    overflow: hidden;
    box-shadow: 0 6px 18px rgba(0,0,0,0.18);
  }
  .card--front { top: 40px; background: var(--paper); }
  .card--back {
    top: 524px;
    background: radial-gradient(ellipse at 58% 42%, var(--glow) 0%, var(--orange-mid) 35%, var(--red) 75%, var(--red-deep) 100%);
  }

  /* front */
  .brand {
    position: absolute;
    left: 70px;
    top: 52px;
    display: flex;
    align-items: center;
    gap: 22px;
  }
  .brand__dot {
    width: 92px; height: 92px;
    border-radius: 50%;
    background: var(--orange-mid);
  }
  .brand__name {
    font-family: "Arimo", Arial, sans-serif;
    font-weight: 700;
    font-size: 104px;
    letter-spacing: -3px;
    color: var(--logo-grey);
    line-height: 1;
  }
  .band {
    position: absolute;
    left: 0; top: 196px;
    width: 100%; height: 150px;
    background: linear-gradient(90deg, var(--red) 0%, var(--orange-mid) 45%, var(--orange) 100%);
    display: flex;
    align-items: center;
    color: var(--white);
  }
  .person {
    width: 300px;
    text-align: right;
    padding-right: 22px;
    border-right: 2px solid rgba(255,255,255,0.75);
    height: 96px;
    display: flex; flex-direction: column; justify-content: center;
  }
  .person__name { font-weight: 700; font-size: 30px; }
  .person__title { font-size: 22px; margin-top: 4px; }
  .contacts { list-style: none; padding-left: 24px; font-size: 24px; line-height: 1.4; }
  .contacts li { display: flex; align-items: center; gap: 10px; }
  .contacts svg { width: 18px; height: 18px; fill: var(--white); flex: none; }
  .address {
    position: absolute;
    left: 0; right: 0; top: 366px;
    text-align: center;
    font-size: 22px;
    color: var(--ink);
  }

  /* back */
  .mark {
    position: absolute;
    left: 330px; top: 60px;
    display: flex; align-items: center; gap: 16px;
  }
  .mark__dot {
    width: 150px; height: 150px;
    border-radius: 50%;
    background: var(--orange);
  }
  .mark__name {
    font-family: "Arimo", Arial, sans-serif;
    font-weight: 700;
    font-size: 48px;
    color: var(--white);
  }
  .tagline {
    position: absolute;
    left: 0; right: 0; top: 262px;
    text-align: center;
    font-family: "Open Sans", Arial, sans-serif;
    font-size: 27px;
    line-height: 1.3;
    color: var(--white);
  }
</style>
</head>
<body>
  <section class="card card--front" aria-label="Business card front">
    <div class="brand">
      <span class="brand__dot" aria-hidden="true"></span>
      <span class="brand__name">Plavorix</span>
    </div>
    <div class="band">
      <div class="person">
        <p class="person__name">Gerald Pinfold</p>
        <p class="person__title">Vice President</p>
      </div>
      <ul class="contacts">
        <li>
          <svg viewBox="0 0 24 24" aria-hidden="true"><path d="M6.6 10.8a15.1 15.1 0 0 0 6.6 6.6l2.2-2.2a1 1 0 0 1 1-.25 11.4 11.4 0 0 0 3.6.57 1 1 0 0 1 1 1V20a1 1 0 0 1-1 1A17 17 0 0 1 3 4a1 1 0 0 1 1-1h3.5a1 1 0 0 1 1 1c0 1.25.2 2.45.57 3.57a1 1 0 0 1-.25 1z"/></svg>
          866-392-5074(US) TF
        </li>
        <li>
          <svg viewBox="0 0 24 24" aria-hidden="true"><path d="M7 1h10a2 2 0 0 1 2 2v18a2 2 0 0 1-2 2H7a2 2 0 0 1-2-2V3a2 2 0 0 1 2-2zm0 3v14h10V4zm5 15.5a1.2 1.2 0 1 0 0 2.4 1.2 1.2 0 0 0 0-2.4z"/></svg>
          123-456-3190
        </li>
        <li>
          <svg viewBox="0 0 24 24" aria-hidden="true"><path d="M2 5h20v14H2zm2 2v.5l8 5 8-5V7zm0 2.8V17h16V9.8l-8 5z"/></svg>
          gpinfold@plavorix.com
        </li>
      </ul>
    </div>
    <p class="address">4738 W. Harrowgate Lane., STE 305, PMB#417, Mesa, AZ 85374</p>
  </section>

  <section class="card card--back" aria-label="Business card back">
    <div class="mark">
      <span class="mark__dot" aria-hidden="true"></span>
      <span class="mark__name">Plavorix</span>
    </div>
    <p class="tagline">Dependable Drawing File Tools for Architects<br>and Engineers in Every Market</p>
  </section>
</body>
</html>
```